Financial Advisor Resource Firm needs business card design

Need business card design for company in Omaha NE called Meridale Circle. We provide resources to financial advisors....workshop programs, retirement analysis, and insurance planning. I would like to see designs that use grays, greens, black, and white colors. The final design should communicate 'collaboration' and be simple yet attractive to financial planning clients. I will attached our logo and another picture of a puzzle piece coming together. I would like the incorporate the puzzle picture somehow, maybe on the back somehow, with color or just the gray scale....OR, the picture be the front of the card with 'Meridale' definition on it (see upload) and then company logo, employee name, title, address on the back (see ppt uploaded). The following disclosure needs to be included somewhere- Advisory services offered through Stonebrook Assets, LLC.
Updates

I uploaded a svg and ai file of the logo

Target Market(s)

Financial planning clients and financial advisors....so pretty diverse age range of about 40-70.

Industry/Entity Type

Financial Planning

Contact Information for Business Card

Tobias L. Fenwright, MBA
Founder/President
5287 E. Larkin Road
Suite 230
Omaha, NE 68190
Phone- (402) 555-0147
Cell- (402) 555-0183
Fax- (402) 555-0129
email- tobias@meridaleplan.example
web address- www.meridaleplan.example

Colors
1b1b1b
474747
d3d3d3
ffffff
9bcb3c
abd036

Requirements
Must have
• Must include logo provided, must be 2 sided, and must have disclosure...all of these items listed in project description

```html
<!DOCTYPE html>
<html lang="en">
<head>
<meta charset="utf-8">
<title>Meridale Circle — Business Card</title>
<link href="https://fonts.googleapis.com/css2?family=Fira+Sans:wght@400;500;600&display=swap" rel="stylesheet">
<style>
  :root {
    --ink: #1b1b1b;
    --graphite: #474747;
    --silver: #d3d3d3;
    --paper: #ffffff;
    --leaf: #8cc63f;
    --leaf-light: #9bcb3c;
    --leaf-deep: #7cbb2e;
    --stage: #e9e9e9;
  }
  * { box-sizing: border-box; margin: 0; padding: 0; }
  html, body { width: 1200px; height: 900px; overflow: hidden; }
  body {
    background: var(--stage);
    font-family: "Fira Sans", Arial, sans-serif;
    display: flex;
    flex-direction: column;
    align-items: center;
    justify-content: center;
    gap: 40px;
  }
  .card {
    width: 700px;
    height: 400px;
    position: relative;
    box-shadow: 0 6px 18px rgba(0,0,0,0.12);
  }

  /* Contact side */
  .card-front { background: var(--paper); color: var(--ink); }
  .name-marker {
    position: absolute; left: 36px; top: 40px;
    width: 22px; height: 26px;
    background: var(--leaf);
    border-left: 4px solid var(--graphite);
  }
  .identity { position: absolute; left: 72px; top: 36px; }
  .person-name { color: var(--leaf); font-size: 27px; font-weight: 500; letter-spacing: -0.2px; line-height: 1.2; }
  .person-title { color: var(--graphite); font-size: 15px; margin-top: 2px; }
  .divider {
    position: absolute; left: 36px; top: 112px;
    width: 520px; height: 2px; background: var(--leaf);
  }
  .contact-list {
    position: absolute; left: 40px; top: 136px;
    list-style: none; font-size: 16px; color: var(--ink);
  }
  .contact-list li { display: flex; align-items: center; gap: 12px; height: 27px; }
  .contact-list svg { width: 14px; height: 14px; flex: none; }
  .web-accent { color: var(--leaf); }
  .brand-front {
    position: absolute; right: 44px; top: 140px;
    text-align: right; color: var(--ink);
    font-size: 32px; font-weight: 600; letter-spacing: 0.5px; line-height: 1;
  }
  .address {
    position: absolute; right: 44px; bottom: 36px;
    text-align: right; font-size: 17px; line-height: 1.45; color: var(--ink);
    font-style: normal;
  }

  /* Brand side */
  .card-back {
    background: linear-gradient(135deg, var(--leaf-light), var(--leaf-deep));
    display: flex; align-items: center; justify-content: center;
  }
  .brand-back {
    color: var(--paper); font-size: 48px; font-weight: 600; letter-spacing: 1px;
  }
  .disclosure {
    position: absolute; left: 0; right: 0; bottom: 22px;
    text-align: center; color: var(--paper);
    font-size: 12px; font-weight: 400; letter-spacing: 0.3px;
  }
</style>
</head>
<body>

<section class="card card-front" aria-label="Business card, contact side">
  <div class="name-marker"></div>
  <div class="identity">
    <h1 class="person-name">Tobias L. Fenwright, MBA</h1>
    <p class="person-title">Founder/President</p>
  </div>
  <div class="divider"></div>

  <ul class="contact-list">
    <li>
      <svg viewBox="0 0 16 16" aria-hidden="true"><path fill="#8cc63f" d="M3.6 1.5l2.3 2.6-1.3 1.7c.9 2 2.6 3.8 4.6 4.7l1.7-1.3 2.6 2.3-1.5 2.6C7 13.8 2.2 9 1 4z"/></svg>
      (402) 555-0147
    </li>
    <li>
      <svg viewBox="0 0 16 16" aria-hidden="true"><rect x="4" y="1" width="8" height="14" rx="1.5" fill="none" stroke="#8cc63f" stroke-width="1.6"/><circle cx="8" cy="12.3" r="1" fill="#8cc63f"/></svg>
      (402) 555-0183
    </li>
    <li>
      <svg viewBox="0 0 16 16" aria-hidden="true"><rect x="4" y="1.5" width="8" height="4" fill="#8cc63f"/><rect x="1.5" y="6" width="13" height="6" rx="1" fill="#8cc63f"/><rect x="4" y="10" width="8" height="4.5" fill="#fff" stroke="#8cc63f" stroke-width="1.2"/></svg>
      (402) 555-0129
    </li>
    <li>
      <svg viewBox="0 0 16 16" aria-hidden="true"><rect x="1.5" y="3.5" width="13" height="9" rx="1" fill="none" stroke="#8cc63f" stroke-width="1.6"/><path d="M2 4l6 5 6-5" fill="none" stroke="#8cc63f" stroke-width="1.6"/></svg>
      tobias@meridaleplan.example
    </li>
    <li>
      <svg viewBox="0 0 16 16" aria-hidden="true"><circle cx="8" cy="8" r="6.3" fill="none" stroke="#8cc63f" stroke-width="1.5"/><ellipse cx="8" cy="8" rx="2.6" ry="6.3" fill="none" stroke="#8cc63f" stroke-width="1.2"/><path d="M1.8 8h12.4" stroke="#8cc63f" stroke-width="1.2"/></svg>
      <span>www.<span class="web-accent">meridaleplan</span>.example</span>
    </li>
  </ul>

  <p class="brand-front">Meridale Circle</p>

  <address class="address">
    5287 E. Larkin Road<br>
    Suite 230 Omaha, NE 68190
  </address>
</section>

<section class="card card-back" aria-label="Business card, brand side">
  <p class="brand-back">Meridale Circle</p>
  <p class="disclosure">Advisory services offered through Stonebrook Assets, LLC.</p>
</section>

</body>
</html>
```